Business Card for a Dental Office

The design should communicate integrity, quality and reliability. We also want the card look elegant, simple, but still stand out, different from the traditional-dental-office business card.

Industry/Entity Type

Business

```html
<!DOCTYPE html>
<html lang="en">
<head>
<meta charset="utf-8">
<title>Marlow Dental Centre – Business Card</title>
<link href="https://fonts.googleapis.com/css2?family=Open+Sans:wght@400;600;700&display=swap" rel="stylesheet">
<style>
  :root{
    --stage:#e9e7e2;
    --yellow-light:#f8f134;
    --yellow-deep:#e6d21a;
    --gold:#c9a816;
    --ink:#141414;
    --text:#2b2b2b;
    --paper:#ffffff;
    --mist:#ececec;
  }
  *{box-sizing:border-box;margin:0;padding:0}
  html,body{width:1200px;height:900px;overflow:hidden}
  body{background:var(--stage);position:relative;font-family:"Open Sans",sans-serif}
  .card{position:absolute;top:300px;width:520px;height:300px;box-shadow:0 6px 18px rgba(0,0,0,.18);overflow:hidden}
  .card--front{left:50px;background:linear-gradient(200deg,var(--yellow-light) 0%,var(--yellow-light) 45%,var(--yellow-deep) 100%)}
  .card--back{left:630px;background:var(--paper)}
  .front-shade{position:absolute;left:0;top:0;width:260px;height:300px;background:linear-gradient(90deg,rgba(200,180,10,.28),rgba(200,180,10,0))}
  .front-brand{position:absolute;right:28px;bottom:82px;text-align:right}
  .front-name{font-weight:700;font-size:29px;line-height:1.1;color:var(--ink);letter-spacing:.3px}
  .front-slogan{font-weight:600;font-size:13px;color:var(--ink);letter-spacing:1.4px;margin-top:4px}
  .back-fade{position:absolute;left:0;top:90px;width:260px;height:210px;background:linear-gradient(160deg,var(--mist),rgba(236,236,236,0))}
  .back-brand{position:absolute;left:26px;top:38px;display:flex;align-items:center;gap:10px}
  .brand-square{width:26px;height:26px;background:var(--ink)}
  .back-name{font-weight:700;font-size:20px;line-height:1;color:var(--ink);letter-spacing:.3px}
  .contact{position:absolute;left:300px;top:108px;color:var(--text);font-size:12.5px;line-height:1.45}
  .contact-name{font-weight:600;font-size:16px;color:var(--gold)}
  .contact-role{margin-bottom:12px}
  .contact-address{margin-bottom:12px}
  .contact-line{display:flex;align-items:center;gap:9px}
  .contact-line svg{width:11px;height:11px;flex:none}
</style>
</head>
<body>
  <section class="card card--front">
    <div class="front-shade"></div>
    <div class="front-brand">
      <div class="front-name">MARLOW DENTAL CENTRE</div>
      <div class="front-slogan">GENTLE CARE FOR EVERY SMILE</div>
    </div>
  </section>

  <section class="card card--back">
    <div class="back-fade"></div>
    <div class="back-brand">
      <span class="brand-square"></span>
      <div class="back-name">MARLOW DENTAL CENTRE</div>
    </div>
    <div class="contact">
      <div class="contact-name">Daniel Hartley</div>
      <div class="contact-role">Managing Director</div>
      <div class="contact-address">12345, Address Goes Here<br>Country Name, 123456.</div>
      <div class="contact-line">
        <svg viewBox="0 0 24 24"><path fill="#c9a816" d="M6.6 10.8a15 15 0 0 0 6.6 6.6l2.2-2.2c.3-.3.7-.4 1-.2 1.1.4 2.300.6 3.6.6.6 0 1 .4 1 1V20c0 .6-.4 1-1 1A17 17 0 0 1 3 4c0-.6.4-1 1-1h3.5c.6 0 1 .4 1 1 0 1.3.2 2.5.6 3.6.1.3 0 .7-.2 1z"/></svg>
        <span>044-555 018 274</span>
      </div>
      <div class="contact-line">
        <svg viewBox="0 0 24 24"><path fill="#c9a816" d="M2 5h20v14H2z"/><path fill="none" stroke="#fff" stroke-width="2" d="M3 6l9 7 9-7"/></svg>
        <span>hello@marlowdental.com</span>
      </div>
      <div class="contact-line">
        <svg viewBox="0 0 24 24"><g fill="none" stroke="#c9a816" stroke-width="3" stroke-linecap="round"><path d="M10 14l4-4"/><path d="M8 12l-3 3a3 3 0 0 0 4 4l3-3"/><path d="M16 12l3-3a3 3 0 0 0-4-4l-3 3"/></g></svg>
        <span>www.marlowdental.com</span>
      </div>
    </div>
  </section>
</body>
</html>
```